New, modern business card for growing audiology practice

We need a new business card for our audiology practice. Our logo and website have recently changed (more modern) and we want our business cards to reflect this change.
We conduct hearing tests, perform earwax removals, and fit & dispense hearing aids to our patients. We are a family owned practice in which the owner is the one who works directly with the patient. I have attached logos in various formats to use, as well as two ideas I found on this website; as well as a scanned copy of our current logo. Good luck!

Industry/Entity Type

Business

Contact Information for Business Card

Company name: Tolvera Hearing Center
Provider name: Peter Wolstenby, Au.D. F/NSB
Phone number: (440) 683-5127
Address: 837 W. Lindell Ave. Brenmoor Falls, OH 44318
email: tolverahearing@postvane.com
website: tolverahearing.com

Colors
000000
aaaaaa
dbdbdb
cacaca
9bcb3c
afd23c
cadf82
b1b1b1

Requirements
Must have
• My card must include information in the "details" section. In the attached images, I found a few that I liked and I would like to model after - "brisky bouncin'" and "Sound Method Center".
• Must be horizontal.
• Must include logos provided. I uploaded them in various file formats and various ways.
• Must match logo font, if possible, if not, please get as close as you can.
Nice to have
• I really like the idea of having a color on one side with just the logo and company name and the contact information and provider name on the other side. I also really like the idea of having the main color dominating on the logo/company side with accent of that same color on the contact side of the card.
Should not have
• Must not be vertical.

```html
<!DOCTYPE html>
<html lang="en">
<head>
<meta charset="utf-8">
<title>Tolvera Hearing Center — Business Card</title>
<link href="https://fonts.googleapis.com/css2?family=Lato:wght@300;400;700&display=swap" rel="stylesheet">
<style>
  :root {
    --canvas-bg: #2b2b2b;
    --card-black: #0c0c0c;
    --card-edge: #1a1a1a;
    --lime: #9bcb3c;
    --lime-bright: #afd23c;
    --lime-soft: #cadf82;
    --text-white: #f2f2f2;
    --text-grey: #b1b1b1;
    --text-mid: #aaaaaa;
  }
  * { box-sizing: border-box; margin: 0; padding: 0; }
  html, body {
    width: 1200px; height: 900px; overflow: hidden;
    background: var(--canvas-bg);
    font-family: "Lato", sans-serif;
  }
  .canvas {
    position: relative; width: 1200px; height: 900px;
    display: flex; align-items: center; justify-content: center; gap: 30px;
  }
  .card {
    position: relative; width: 550px; height: 314px;
    background: var(--card-black);
    border-radius: 18px;
    box-shadow: 0 0 0 1px var(--card-edge), 0 18px 40px rgba(0,0,0,.45);
    color: var(--text-white);
    overflow: hidden;
  }

  /* Contact side */
  .brand-mark {
    position: absolute; top: 28px; right: 34px;
    display: flex; align-items: center; gap: 8px;
    font-size: 12px; letter-spacing: .5px; font-weight: 400;
    color: var(--text-white); text-transform: uppercase;
  }
  .brand-dot {
    width: 10px; height: 10px; border-radius: 50%;
    background: var(--lime);
  }
  .provider { position: absolute; top: 100px; left: 40px; }
  .provider-name {
    font-weight: 700; font-size: 16px; letter-spacing: .4px;
    color: var(--lime-bright); text-transform: uppercase;
  }
  .provider-role { margin-top: 3px; font-size: 12px; color: var(--text-grey); font-weight: 300; }
  .edge-tab {
    position: absolute; left: 0; top: 122px; width: 14px; height: 22px;
    background: var(--lime); border-left: 7px solid #fff;
  }
  .address {
    position: absolute; top: 190px; right: 34px; text-align: right;
    font-style: normal;
    font-size: 13px; line-height: 1.4; color: var(--text-white); font-weight: 300;
  }
  .contact-list {
    position: absolute; left: 40px; bottom: 32px; list-style: none;
    font-size: 14px; line-height: 1.4; font-weight: 300;
  }
  .contact-item { display: flex; align-items: center; gap: 12px; }
  .contact-icon { width: 10px; height: 10px; flex: none; }
  .web-name { color: var(--lime-bright); }

  /* Logo side */
  .logo-line {
    position: absolute; top: 116px; left: 0; right: 0;
    display: flex; align-items: center; justify-content: center; gap: 14px;
  }
  .logo-dot {
    width: 20px; height: 20px; border-radius: 50%; background: var(--lime);
  }
  .logo-name {
    font-size: 26px; font-weight: 400; letter-spacing: .6px;
    color: var(--text-white); text-transform: uppercase;
  }
  .front-rule { position: absolute; left: 0; top: 160px; width: 550px; height: 80px; }
  .front-url {
    position: absolute; top: 206px; left: 300px;
    font-size: 10px; color: var(--text-mid); font-weight: 300;
  }
  .front-url .web-name { color: var(--lime-soft); }
</style>
</head>
<body>
<main class="canvas">

  <section class="card card-back" aria-label="Contact side">
    <div class="brand-mark"><span class="brand-dot"></span>Tolvera Hearing Center</div>

    <span class="edge-tab"></span>
    <div class="provider">
      <p class="provider-name">Peter Wolstenby, Au.D. F/NSB</p>
      <p class="provider-role">Owner-Audiologist</p>
    </div>

    <address class="address">
      837 W. Lindell Ave.<br>Brenmoor Falls, OH 44318
    </address>

    <ul class="contact-list">
      <li class="contact-item">
        <svg class="contact-icon" viewBox="0 0 10 10"><path d="M2 0.5 L3.6 2.6 L2.6 3.6 Q3.6 5.8 6.4 7.4 L7.4 6.4 L9.5 8 L8 9.5 Q3 9 0.5 2 Z" fill="#9bcb3c"/></svg>
        <span>(440) 683-5127</span>
      </li>
      <li class="contact-item">
        <svg class="contact-icon" viewBox="0 0 10 10"><rect x="0.5" y="2" width="9" height="6.5" fill="none" stroke="#9bcb3c" stroke-width="1.2"/><path d="M0.5 2 L5 6 L9.5 2" fill="none" stroke="#9bcb3c" stroke-width="1.2"/></svg>
        <span>tolverahearing@postvane.com</span>
      </li>
      <li class="contact-item">
        <svg class="contact-icon" viewBox="0 0 10 10"><circle cx="5" cy="5" r="4.3" fill="none" stroke="#9bcb3c" stroke-width="1.2"/><path d="M0.7 5 H9.3 M5 0.7 Q2 5 5 9.3 M5 0.7 Q8 5 5 9.3" fill="none" stroke="#9bcb3c" stroke-width="0.9"/></svg>
        <span>www.<span class="web-name">tolverahearing</span>.com</span>
      </li>
    </ul>
  </section>

  <section class="card card-front" aria-label="Logo side">
    <div class="logo-line">
      <span class="logo-dot"></span>
      <span class="logo-name">Tolvera Hearing Center</span>
    </div>
    <svg class="front-rule" viewBox="0 0 550 80" aria-hidden="true">
      <path d="M340 22 L470 18 L472 19 L340 23.5 Z" fill="#9bcb3c"/>
      <path d="M160 52 L292 50 L292 51.5 L160 54.5 Z" fill="#9bcb3c"/>
    </svg>
    <p class="front-url">www.<span class="web-name">tolverahearing</span>.com</p>
  </section>

</main>
</body>
</html>
```